Professional, Attractive, Simple Website Needed!!

We completed the design for our logo.

We need a website built out around this.

Here are a couple samples of how we want ours formatted.

http://brimvoltco.com

http://www.ravelbeam.com/lp/free-quote?LeadSource=Search%20Engine&ProgramName=searchads&experience=qual&language=en&type=brd&gclid=Xk7PLmqwTRZBNVuEYcaHdFgWsLoPeRtQnMxVbCzJaKiOuYtReWqAsDfGhJkLzXcVbNmQwErTyUiOpAsDfGhJkLzX_wcB

http://quorel.co
Updates

Project Deadline Extended
Reason: Extending this deadline due to our delay in providing designers with content for each page. This is coming in next 24 hours.

Project Deadline Extended
Reason: Due to scheduling conflicts and extended travel delays related to Puerto Rico, the deadline has been extended. Your patience is greatly appreciated.

Project Deadline Extended
Reason: Travel and scheduling conflicts have made it impossible to give this project the thorough review it deserves, therefore I am extending the deadline. Thank you for your patience!

Target Market(s)

Home Owners who earn 60k + household annually

Industry/Entity Type

It Professional

Coding

Coded - Design and coding required

Number of Pages Required

5+ page

Font styles to use
Serif

Colors
34a7d8
9bcb3c

Requirements
Must have
• Simple
• Lead form Entry (Ability for visitor to enter Name, number and address for a quote)
• Sleek Design
• Professional
• Testimonials
• Use color Scheme of Design Logo Attached
Nice to have
• Video when site starts
• Like this
• https://www.vidplexa.com/watch?v=Qm8rTbLw3Np&feature=vidplexa.be
Should not have
• Should not include Commercial solar
• Should not include wind power

```html
<!DOCTYPE html>
<html lang="en">
<head>
<meta charset="utf-8">
<title>Clear Sky Energy – Solar Savings</title>
<link rel="stylesheet" href="https://fonts.googleapis.com/css2?family=Montserrat:ital,wght@0,400;0,500;0,600;0,700&family=Arimo:ital,wght@0,400;0,700;1,400&display=swap">
<style>
:root{
  --blue:#1a9bd6;
  --blue-deep:#0f8fc8;
  --teal:#3aa59a;
  --green:#9bcb3c;
  --green-text:#8cc63f;
  --green-bright:#c6e879;
  --white:#ffffff;
  --ink:#555a5e;
  --mist:#e7f0f5;
  --border-soft:#6fc3e6;
}
*{box-sizing:border-box;margin:0;padding:0}
html,body{width:1200px;height:3636px;overflow:hidden}
body{position:relative;background:var(--white);font-family:"Arimo",Arial,sans-serif;color:var(--ink)}
.abs{position:absolute}
.backdrop{position:absolute;left:0;top:0}

/* nav */
.topbar{left:0;top:0;width:1200px;height:63px;background:var(--blue)}
.nav{left:0;top:0;height:63px;width:1200px;font-family:"Montserrat",sans-serif;font-weight:500;font-size:18px;color:var(--white)}
.nav a{position:absolute;top:20px;color:var(--white);text-decoration:none;white-space:nowrap}
.nav a.active{color:var(--green);border-bottom:2px solid var(--white);padding-bottom:10px}
.call-btn{left:967px;top:12px;width:153px;height:40px;border-radius:20px;background:var(--white);color:var(--blue);font-family:"Montserrat",sans-serif;font-weight:600;font-size:15px;display:flex;align-items:center;justify-content:center;gap:8px}

/* hero */
.hero-photo{left:0;top:63px;width:1200px;height:737px;
  background:radial-gradient(ellipse 380px 260px at 300px 300px,rgba(255,214,150,.95),rgba(240,160,90,.55) 45%,rgba(0,0,0,0) 75%),
  linear-gradient(180deg,#5f7fa5 0%,#a9a2a6 28%,#d89a64 44%,#3b5876 62%,#1f3a5a 100%)}
.brand-mark{left:0;top:230px;width:1200px;display:flex;align-items:center;justify-content:center;gap:22px}
.brand-mark .ring{width:96px;height:96px;border-radius:50%;border:8px solid var(--white)}
.brand-mark .name{font-family:"Montserrat",sans-serif;font-weight:600;font-size:52px;color:var(--white);letter-spacing:1px}
.hero-title{left:0;top:520px;width:1200px;text-align:center;font-family:"Montserrat",sans-serif;font-weight:500;font-size:41px;color:var(--white);letter-spacing:1px}
.pill{top:771px;height:58px;border-radius:29px;background:var(--blue);border:4px solid var(--white);color:var(--white);font-family:"Montserrat",sans-serif;font-weight:500;font-size:21px;display:flex;align-items:center;justify-content:center;box-shadow:0 3px 6px rgba(0,0,0,.25)}
.hero-copy{left:0;top:860px;width:1200px;text-align:center;color:var(--white);font-size:21px;line-height:32px}

/* video */
.video{left:262px;top:1052px;width:676px;height:417px;background:linear-gradient(135deg,#4c5a4e 0%,#2d3532 50%,#1b2226 100%);display:flex;align-items:center;justify-content:center}
.play{width:90px;height:90px;border-radius:50%;background:rgba(255,255,255,.9);display:flex;align-items:center;justify-content:center}

/* section titles */
.title{left:0;width:1200px;text-align:center;font-family:"Montserrat",sans-serif}
.title .main{font-size:40px;font-weight:500;line-height:46px;letter-spacing:1px}
.title .main .b{color:var(--blue)}
.title .main .g{color:var(--green-text)}
.title .sub{display:flex;align-items:center;justify-content:center;gap:10px;font-size:20px;color:var(--green-text);letter-spacing:2px;line-height:24px}
.title .sub::before,.title .sub::after{content:"";width:70px;height:1px;background:var(--green-text)}
/* titles that sit on the gradient bands */
.title.on-band .main .b{color:var(--white)}
.title.on-band .main .g,.title.on-band .sub{color:var(--green-bright)}
.title.on-band .sub::before,.title.on-band .sub::after{background:var(--green-bright)}

.why-copy{left:210px;top:1690px;width:780px;text-align:center;color:var(--white);font-size:15px;line-height:25px}

/* how it works */
.how-photo{left:0;top:1842px;width:1200px;height:514px;background:linear-gradient(160deg,#f3f7fa 0%,#dde9f1 45%,#efe3dc 75%,#e3eef2 100%)}
.step{width:146px;height:146px;border-radius:50%;background:var(--white);border:3px solid var(--blue);display:flex;align-items:center;justify-content:center;box-shadow:0 6px 8px rgba(0,0,0,.15)}
.step-label{width:240px;text-align:center;font-family:"Montserrat",sans-serif;font-weight:500;font-size:19px;color:var(--blue)}
.hub{left:509px;top:2145px;width:180px;height:180px;border-radius:50%;background:var(--white);border:4px solid var(--green);display:flex;align-items:center;justify-content:center;text-align:center;font-family:"Montserrat",sans-serif;font-weight:600;font-size:22px;line-height:27px;color:var(--blue);box-shadow:0 6px 10px rgba(0,0,0,.18)}

/* blog */
.post-photo{width:238px;height:135px}
.post-photo.roof{background:linear-gradient(180deg,#6aa5d6 0%,#9cc1dc 35%,#b45b33 55%,#2f4a7a 80%,#3f6a3a 100%)}
.post-photo.array{background:linear-gradient(180deg,#3c7fd0 0%,#8ab8e2 45%,#3f6a3a 70%,#2a3f5a 100%)}
.post-text{width:230px;color:var(--white)}
.post-text .date{font-size:15px;line-height:20px}
.post-text h3{font-size:17px;font-weight:700;line-height:24px}
.post-text p{font-size:15px;line-height:24px;color:rgba(255,255,255,.78)}

/* testimonials */
.avatar{left:538px;top:2819px;width:122px;height:122px;border-radius:50%;border:3px dashed var(--blue);padding:6px}
.avatar .photo{width:100%;height:100%;border-radius:50%;background:radial-gradient(circle at 50% 45%,#f1d2b6,#d9a77a 60%,#b98b5f)}
.quote{left:213px;top:2962px;width:776px;height:116px;border:2px solid var(--border-soft);display:flex;align-items:center;justify-content:center;text-align:center;padding:0 30px;font-style:italic;font-size:15px;line-height:24px;color:#7a8086}
.arrow{top:3005px;width:32px;height:34px;background:var(--border-soft);display:flex;align-items:center;justify-content:center}
.dot{top:3108px;width:14px;height:14px;border-radius:50%;background:#b9bcbf}
.dot.on{background:var(--blue)}

/* lead form */
.lead-form{left:228px;top:3321px;width:744px;height:206px;background:rgba(255,255,255,.18)}
.input{height:42px;border:2px solid var(--blue);background:rgba(255,255,255,.12);color:var(--blue);font-size:15px;padding-left:10px;display:flex;align-items:center}
.login{left:521px;top:3464px;width:155px;height:41px;border-radius:21px;background:var(--blue);color:var(--white);font-family:"Montserrat",sans-serif;font-size:18px;display:flex;align-items:center;justify-content:center;letter-spacing:1px}
.footer-rule{left:75px;top:3580px;width:1050px;height:1px;background:rgba(255,255,255,.35)}
.copyright{left:0;top:3598px;width:1200px;text-align:center;color:var(--white);font-size:16px}
.copyright span{color:var(--green-bright)}
</style>
</head>
<body>

<svg class="backdrop" width="1200" height="3636" viewBox="0 0 1200 3636" aria-hidden="true">
  <defs>
    <linearGradient id="band" x1="0" y1="0" x2="1" y2="0">
      <stop offset="0" stop-color="#0f8fc8"/>
      <stop offset=".5" stop-color="#3aa59a"/>
      <stop offset="1" stop-color="#9bcb3c"/>
    </linearGradient>
  </defs>
  <path d="M0 800 H1200 V960 Q600 1080 0 960 Z" fill="url(#band)"/>
  <path d="M0 1505 Q600 1580 1200 1505 V1842 H0 Z" fill="url(#band)"/>
  <path d="M0 2356 H1200 V2670 Q600 2750 0 2690 Z" fill="url(#band)"/>
  <path d="M0 3150 Q600 3085 1200 3140 V3636 H0 Z" fill="url(#band)"/>
</svg>

<header>
  <div class="abs topbar"></div>
  <nav class="abs nav">
    <a class="active" style="left:80px">Home</a>
    <a style="left:167px">Why Clear Sky Energy</a>
    <a style="left:390px">How It Works</a>
    <a style="left:538px">Testimonials</a>
    <a style="left:686px">Blog</a>
    <a style="left:763px">Contact</a>
  </nav>
  <div class="abs call-btn">
    <svg width="16" height="16" viewBox="0 0 24 24"><path fill="currentColor" d="M6.6 10.8a15 15 0 0 0 6.6 6.6l2.2-2.2a1 1 0 0 1 1-.25 11.4 11.4 0 0 0 3.6.57 1 1 0 0 1 1 1V20a1 1 0 0 1-1 1A17 17 0 0 1 3 4a1 1 0 0 1 1-1h3.5a1 1 0 0 1 1 1c0 1.250.2 2.45.57 3.57a1 1 0 0 1-.25 1z"/></svg>
    CALL NOW
  </div>
</header>

<section class="hero">
  <div class="abs hero-photo" role="img" aria-label="Sunset sky over rows of rooftop solar panels"></div>
  <div class="abs brand-mark"><div class="ring"></div><div class="name">CLEAR SKY ENERGY</div></div>
  <h1 class="abs hero-title">SOLAR SAVINGS WITH CLEAR SKY ENERGY</h1>
  <div class="abs pill" style="left:138px;width:289px">Zero Cost</div>
  <div class="abs pill" style="left:456px;width:288px">Lower Energy Bills</div>
  <div class="abs pill" style="left:768px;width:289px">No Maintenance</div>
  <p class="abs hero-copy">Lorem Ipsum is simply dummy text of the printing and typesetting industry.<br>Lorem Ipsum has been the industry's standard dummy text.</p>
</section>

<section class="intro-video">
  <div class="abs video" role="img" aria-label="Video still of an installer fitting solar panels on a roof">
    <div class="play"><svg width="36" height="40" viewBox="0 0 36 40"><path d="M4 2 L34 20 L4 38 Z" fill="#1a9bd6"/></svg></div>
  </div>
</section>

<section class="why">
  <div class="abs title on-band" style="top:1606px">
    <div class="main"><span class="b">WHY </span><span class="g">CLEAR SKY</span></div>
    <div class="sub">ENERGY</div>
  </div>
  <p class="abs why-copy">Lorem Ipsum is simply dummy text of the printing and typesetting industry. Lorem Ipsum has been the industry's standard dummy text ever since the 1500s, when an unknown printer took a galley of type and scrambled it to make a type specimen book. It has survived not only five centuries, but also the leap into electronic typesetting, remaining essentially unchanged.</p>
</section>

<section class="how">
  <div class="abs how-photo" role="img" aria-label="Faded photo of solar panels on a tiled house roof"></div>
  <div class="abs title" style="top:1878px">
    <div class="main"><span class="b">HOW </span><span class="g">IT</span></div>
    <div class="sub">WORKS</div>
  </div>

  <div class="abs step" style="left:426px;top:1963px">
    <svg width="70" height="56" viewBox="0 0 70 56"><g fill="none" stroke="#1a9bd6" stroke-width="3"><path d="M8 40 L18 12 H60 L64 40 Z"/><path d="M12 30 H63 M15 21 H61 M32 12 L30 40 M46 12 L48 40"/><path d="M36 40 V50 M24 52 H48"/></g><circle cx="58" cy="8" r="6" fill="#9bcb3c"/></svg>
  </div>
  <div class="abs step-label" style="left:379px;top:2124px">Design</div>

  <div class="abs step" style="left:635px;top:1963px">
    <svg width="58" height="58" viewBox="0 0 58 58"><rect x="5" y="10" width="48" height="42" rx="4" fill="none" stroke="#1a9bd6" stroke-width="3"/><rect x="5" y="10" width="48" height="10" fill="#1a9bd6"/><path d="M16 4 V14 M42 4 V14" stroke="#1a9bd6" stroke-width="4"/><g fill="#1a9bd6"><rect x="12" y="26" width="8" height="7"/><rect x="25" y="26" width="8" height="7"/><rect x="38" y="26" width="8" height="7"/><rect x="12" y="38" width="8" height="7"/><rect x="25" y="38" width="8" height="7"/><rect x="38" y="38" width="8" height="7" fill="#9bcb3c"/></g></svg>
  </div>
  <div class="abs step-label" style="left:588px;top:2124px">Schedule</div>

  <div class="abs step" style="left:295px;top:2145px">
    <svg width="58" height="58" viewBox="0 0 58 58"><path d="M14 4 H50 a4 4 0 0 1 4 4 V28 a4 4 0 0 1 -4 4 H34 L26 40 V32 H14 a4 4 0 0 1 -4 -4 V8 a4 4 0 0 1 4 -4Z" fill="#1a9bd6"/><path d="M18 13 H46 M18 21 H40" stroke="#fff" stroke-width="3"/><circle cx="14" cy="42" r="6" fill="#1a9bd6"/><path d="M2 58 a12 10 0 0 1 24 0Z" fill="#1a9bd6"/></svg>
  </div>
  <div class="abs step-label" style="left:248px;top:2308px">Speak Consultant</div>

  <div class="abs step" style="left:746px;top:2145px">
    <svg width="60" height="60" viewBox="0 0 60 60"><circle cx="34" cy="18" r="14" fill="#1a9bd6"/><text x="34" y="24" text-anchor="middle" font-family="Arimo, sans-serif" font-weight="700" font-size="18" fill="#fff">$</text><path d="M4 44 H16 L28 40 H40 a3 3 0 0 1 0 6 H28 M16 54 H40 L56 42 a3 3 0 0 0 -4 -4 L42 44" fill="none" stroke="#1a9bd6" stroke-width="4" stroke-linejoin="round"/></svg>
  </div>
  <div class="abs step-label" style="left:699px;top:2306px">Start Savings</div>

  <div class="abs hub">CLEAR SKY<br>ENERGY</div>
</section>

<section class="blog">
  <div class="abs title on-band" style="top:2399px">
    <div class="main"><span class="b">LATEST</span></div>
    <div class="sub">BLOG</div>
  </div>
  <div class="abs post-photo roof" style="left:102px;top:2490px" role="img" aria-label="Photo of solar panels on a red tile roof"></div>
  <div class="abs post-text" style="left:351px;top:2488px">
    <div class="date">March 29, 2017</div>
    <h3>Lorem Ipsum is simply dummy text</h3>
    <p>Lorem Ipsum is simply dummy text of the printing and typesetting industry.</p>
  </div>
  <div class="abs post-photo array" style="left:637px;top:2490px" role="img" aria-label="Photo of a home solar array under a blue sky"></div>
  <div class="abs post-text" style="left:880px;top:2488px">
    <div class="date">March 29, 2017</div>
    <h3>Lorem Ipsum is simply dummy text</h3>
    <p>Lorem Ipsum is simply dummy text of the printing and typesetting industry.</p>
  </div>
</section>

<section class="testimonials">
  <div class="abs title" style="top:2724px">
    <div class="main"><span class="b">WHAT </span><span class="g">OUR CLIENT</span></div>
    <div class="sub">SAY</div>
  </div>
  <div class="abs avatar"><div class="photo" role="img" aria-label="Client portrait"></div></div>
  <blockquote class="abs quote">It is a long established fact that a reader will be distracted by the readable content of a page when looking at its layout. The point of using Lorem Ipsum is that it has a more-or-less normal distribution of letters, as opposed to using 'Content here, content here', making it look like readable English.</blockquote>
  <div class="abs arrow" style="left:182px"><svg width="12" height="16" viewBox="0 0 12 16"><path d="M9 2 L3 8 L9 14" fill="none" stroke="#fff" stroke-width="3"/></svg></div>
  <div class="abs arrow" style="left:982px"><svg width="12" height="16" viewBox="0 0 12 16"><path d="M3 2 L9 8 L3 14" fill="none" stroke="#fff" stroke-width="3"/></svg></div>
  <div class="abs dot" style="left:555px"></div>
  <div class="abs dot" style="left:590px"></div>
  <div class="abs dot on" style="left:624px"></div>
</section>

<section class="contact">
  <div class="abs title on-band" style="top:3219px">
    <div class="main"><span class="b">SOLAR </span><span class="g">WORKS FOR</span></div>
    <div class="sub">YOU</div>
  </div>
  <form class="abs lead-form">
    <div class="abs input" style="left:27px;top:19px;width:332px">Name</div>
    <div class="abs input" style="left:380px;top:19px;width:333px">Phone</div>
    <div class="abs input" style="left:27px;top:80px;width:686px">Email</div>
  </form>
  <div class="abs login">LOGIN</div>
  <div class="abs footer-rule"></div>
  <footer class="abs copyright">©<span>Clear Sky Energy</span> 2017 - All Rights Reserved.</footer>
</section>

</body>
</html>
```